New Joomla Website for Marquee Hire Co

We need a web design for our new Marquee Hire Co here in New Zealand called Breezy Canopies.
We rather like the retro look, as it fit very well with the current trends in weddings that is a more of a retro look (and we had our logo designed to reflect that!). The 50's and 60's wedding styles are really making a comeback. We would like to communicate to that market effectively.

The Home page should have a slider image with space for a headline on it. It is a visual product we have (but we are selling that dream of a perfect wedding/party/event).

Our competition here have a really nice site that you could look at - www.plovanto.co.nz

The other pages would have space for a picture, and then a blurb under each element related to it.
We will have a FAQ, Gallery, Hire and Contact us pages - we will add them as we go along.

From a technical perspective, we are using Joomla 2.5 and upwards.

Any questions - let me know. I look forward seeing the designs!

Target Market(s)

Couples looking for a wedding marquee, birthday parties, Corporate events

Industry/Entity Type

Wedding

Requirements
Must have
• 1. Preferably done in Joomla. I will also look at Wordpress site.
2. It has to have a retro look and feel.
3. It has to use my brand new logo (included)

```html
<!DOCTYPE html>
<html lang="en">
<head>
<meta charset="utf-8">
<title>Breezy Canopies – Marquee Hire New Zealand</title>
<link rel="stylesheet" href="https://fonts.googleapis.com/css2?family=Lobster&family=Questrial&family=Tinos&family=Open+Sans:ital@1&display=swap">
<style>
:root{
  --paper:#f3f3f1;
  --brown:#65401f;
  --brown-dark:#4e3016;
  --teal-deep:#468ba6;
  --teal:#4a8ea8;
  --teal-mid:#66a4bd;
  --teal-soft:#79b5cb;
  --teal-pale:#94c9dc;
  --cream:#f5e8d2;
  --ink:#5a3a1d;
  --link:#4f97b4;
  --sky-blue:#a9c9e3;
  --white:#ffffff;
}
*{margin:0;padding:0;box-sizing:border-box}
html,body{width:998px;height:1200px;overflow:hidden}
body{background:var(--paper);position:relative;font-family:'Questrial',sans-serif;color:var(--ink)}
.abs{position:absolute}

/* header navigation */
.nav-disc{position:absolute;border-radius:50%;display:flex;align-items:center;justify-content:center;
  font-family:'Lobster',cursive;color:var(--white);font-size:19px;box-shadow:0 3px 6px rgba(0,0,0,.18);
  border:3px dotted rgba(255,255,255,.25)}
.nav-disc.contact{background:var(--brown);width:130px;height:130px;left:707px;top:58px}
.nav-disc.hire{background:var(--teal-pale);width:132px;height:132px;left:608px;top:57px;justify-content:flex-end;padding-right:22px}
.nav-disc.gallery{background:var(--teal-soft);width:132px;height:132px;left:531px;top:57px;justify-content:flex-end;padding-right:26px}
.nav-disc.faq{background:var(--teal-mid);width:132px;height:132px;left:443px;top:57px;justify-content:flex-end;padding-right:36px}
.nav-disc.home{background:var(--teal-deep);width:150px;height:150px;left:333px;top:42px}
.brand{position:absolute;left:225px;top:45px;width:150px;height:150px;border-radius:50%;background:var(--cream);
  border:8px solid var(--teal-mid);display:flex;align-items:center;justify-content:center;box-shadow:0 3px 6px rgba(0,0,0,.2)}
.brand-name{font-family:'Lobster',cursive;color:var(--brown);font-size:22px;line-height:1.05;text-align:center}

.rule{position:absolute;left:0;width:998px;border-top:1px dotted #a9a9a9}

/* hero */
.hero-band{position:absolute;left:0;top:250px;width:998px;height:346px;background:var(--brown)}
.hero-photo{position:absolute;left:92px;top:265px;width:815px;height:317px;
  background:linear-gradient(180deg,#9cbbd6 0%,#c9d9e4 38%,#e9ebe6 55%,#a89a74 72%,#7b8a3e 100%)}
.hero-arrow{position:absolute;top:402px}
.hero-title{position:absolute;left:121px;top:445px;height:39px;padding:0 13px;background:rgba(255,255,255,.72);
  font-family:'Lobster',cursive;font-size:27px;color:var(--ink);line-height:39px}
.hero-title u{text-decoration-thickness:1px;text-underline-offset:4px}
.hero-lead{position:absolute;left:121px;top:493px;width:368px;height:58px;padding:8px 13px;background:rgba(255,255,255,.72);
  font-family:'Open Sans',sans-serif;font-style:italic;font-size:16px;line-height:20px;color:var(--ink)}
.hero-dots{position:absolute;left:777px;top:535px;display:flex;gap:6px}
.hero-dots span{width:16px;height:16px;border-radius:50%;background:rgba(255,255,255,.75)}
.hero-dots span.active{background:transparent;border:2px solid rgba(255,255,255,.9);box-shadow:inset 0 0 0 2px rgba(255,255,255,.4)}

/* feature cards */
.card{position:absolute;top:637px;width:242px;height:279px;background:var(--white);box-shadow:0 1px 3px rgba(0,0,0,.12)}
.card-head{position:relative;height:50px;background:var(--teal);display:flex;align-items:center;justify-content:flex-end;padding-right:15px}
.card-head::after{content:"";position:absolute;left:0;bottom:-5px;width:100%;height:6px;
  background:radial-gradient(circle at 5px 0,var(--teal) 4px,transparent 4.6px) repeat-x;background-size:10px 6px}
.card-tent{position:absolute;left:15px;top:12px;width:56px;height:32px;background:var(--white);border-radius:14px 14px 2px 2px}
.card-title{font-family:'Lobster',cursive;color:var(--white);font-size:24px}
.card-kicker{margin:26px 17px 0;color:var(--link);font-size:13.5px;line-height:19px;text-transform:uppercase}
.card-text{margin:14px 17px 0;font-size:13.5px;line-height:19.5px;text-align:justify;color:var(--ink)}
.card-more{position:absolute;right:11px;bottom:8px;font-family:'Lobster',cursive;font-size:15px;color:var(--link)}
.card-offer{overflow:hidden}
.offer-photo{position:absolute;left:0;top:50px;width:242px;height:229px;
  background:linear-gradient(180deg,#cfdfe8 0%,#ecebe4 35%,#9db2b6 55%,#8b6a44 72%,#667a35 100%)}
.offer-line{position:absolute;width:100%;text-align:center;font-family:'Lobster',cursive;color:var(--white);text-shadow:0 1px 3px rgba(0,0,0,.45)}
.card-offer .card-more{color:var(--white)}

/* footer ribbon */
.ribbon{position:absolute;left:75px;top:945px}

/* footer columns */
.foot-col{position:absolute;top:1006px;width:250px;font-family:'Tinos',serif;font-size:13px;line-height:15px;color:var(--ink)}
.foot-head{display:inline-block;font-family:'Lobster',cursive;font-size:18px;color:var(--sky-blue);padding-bottom:2px;margin-bottom:6px;border-bottom:1px dotted var(--sky-blue)}
.foot-col p+p{margin-top:15px}
.tweet-dot{display:inline-block;width:16px;height:16px;border-radius:50%;background:var(--link);margin-left:14px;vertical-align:2px}

.to-top{position:absolute;left:470px;top:1161px}
.copyright{position:absolute;left:670px;top:1176px;font-size:9px;color:var(--link);font-family:'Questrial',sans-serif}
.copy-mark{position:absolute;left:868px;top:1169px;width:26px;height:18px;background:var(--brown);border-radius:8px 8px 1px 1px}
</style>
</head>
<body>

<header>
  <a class="nav-disc contact">Contact Us</a>
  <a class="nav-disc hire">Hire</a>
  <a class="nav-disc gallery">Gallery</a>
  <a class="nav-disc faq">Faq</a>
  <span class="nav-disc home"></span>
  <div class="brand"><span class="brand-name">Breezy<br>Canopies</span></div>
</header>

<div class="rule" style="top:247px"></div>

<section class="hero-band">
</section>
<div class="hero-photo" role="img" aria-label="White stretch marquee with wicker lounge furniture on a grassy headland overlooking the sea"></div>
<svg class="hero-arrow" style="left:97px" width="14" height="44" viewBox="0 0 14 44"><polygon points="14,0 0,22 14,44" fill="#4a8ea8"/></svg>
<svg class="hero-arrow" style="left:885px" width="14" height="44" viewBox="0 0 14 44"><polygon points="0,0 14,22 0,44" fill="#4a8ea8"/></svg>
<h1 class="hero-title">Contact Us for a <u>Quote</u></h1>
<p class="hero-lead">Have you ever dreamed of getting married by the sea or in the mountains?</p>
<div class="hero-dots"><span class="active"></span><span></span><span></span><span></span></div>

<div class="rule" style="top:599px"></div>

<article class="card card-offer" style="left:97px">
  <div class="card-head"><span class="card-tent" role="img" aria-label="Marquee icon"></span><h2 class="card-title">Special Offers</h2></div>
  <div class="offer-photo" role="img" aria-label="Marquee with wicker sofas by the sea"></div>
  <div class="offer-line" style="top:95px;font-size:22px">Awesome discount!</div>
  <div class="offer-line" style="top:120px;font-size:32px">-20%</div>
  <a class="card-more">More info +</a>
</article>

<article class="card" style="left:384px">
  <div class="card-head"><span class="card-tent" role="img" aria-label="Marquee icon"></span><h2 class="card-title">Lorem Ipsum</h2></div>
  <p class="card-kicker">Tincidunt tempus.<br>Suspendisse ut nisl sapien</p>
  <p class="card-text">Lorem ipsum dolor sit amet, consectetur adipiscing elit. Donec molestie in nisi non consectetur. Nullam dignissim cursus urna ac tempor. Fusce eget arcu nec ipsum</p>
  <a class="card-more">More info +</a>
</article>

<article class="card" style="left:671px">
  <div class="card-head"><span class="card-tent" role="img" aria-label="Marquee icon"></span><h2 class="card-title">Nullam digni</h2></div>
  <p class="card-kicker">Tincidunt tempus.<br>Suspendisse ut nisl sapien</p>
  <p class="card-text">Lorem ipsum dolor sit amet, consectetur adipiscing elit. Donec molestie in nisi non consectetur. Nullam dignissim cursus urna ac tempor. Fusce eget arcu nec ipsum</p>
  <a class="card-more">More info +</a>
</article>

<svg class="ribbon" width="860" height="50" viewBox="0 0 860 50">
  <polygon points="0,38 12,12 30,12 30,38" fill="#4e3016"/>
  <polygon points="860,38 848,12 830,12 830,38" fill="#4e3016"/>
  <polygon points="22,3 838,3 838,35 442,35 428,47 414,35 22,35" fill="#65401f"/>
</svg>

<footer>
  <div class="foot-col" style="left:114px">
    <span class="foot-head">Contact</span>
    <p>18 Kowhai Lane,<br>Raglan, New Zealand</p>
    <p>+64 21 555 0142<br>contact@breezycanopies.co.nz</p>
  </div>
  <div class="foot-col" style="left:386px">
    <span class="foot-head">About</span>
    <p>We are a dedicated team working to take part in your dreamed event project. Breezy Canopies is helping people build memories. Special occasions is worth celebrating.</p>
  </div>
  <div class="foot-col" style="left:658px">
    <span class="foot-head">Recent Tweets</span><span class="tweet-dot"></span>
    <p>2 hours ago : @BreezyCanopies Thank you for your service, it was fabulous!</p>
    <p>A day ago : New discount in Breezy Canopies!</p>
  </div>

  <svg class="to-top" width="66" height="39" viewBox="0 0 66 39"><polygon points="33,0 66,39 0,39" fill="#65401f"/><text x="33" y="33" text-anchor="middle" font-family="Lobster, cursive" font-size="16" fill="#ffffff">Up</text></svg>
  <p class="copyright">© 2013 Breezy Canopies All Rights Reserved</p>
  <span class="copy-mark"></span>
</footer>

</body>
</html>
```